Menu Edit

Hello. We need a pricing edit on our current menu and new logo swapped (we already have the new logo), as well as colour changes. Also, we require a takeaway menu, in-store menu and footpath a-frame edit as well. I have attached the files bellow.

```html
<!DOCTYPE html>
<html lang="en">
<head>
<meta charset="utf-8">
<title>Tide &amp; Tater Fish &amp; Chips – Menu Set</title>
<link rel="stylesheet" href="https://fonts.googleapis.com/css2?family=Cinzel:wght@600&family=Roboto+Slab:wght@400..700&family=Poppins:wght@400;500;600;700&display=swap">
<style>
:root{
  --page:#ffffff;
  --panel:#231f20;
  --ink:#ffffff;
  --muted:#d9d9d9;
  --rule:#8a8a8a;
  --blue:#1b8ff5;
  --badge-green:#06b34f;
  --badge-yellow:#f6d21a;
  --badge-teal:#19c2c9;
  --badge-orange:#f57c12;
  --badge-red:#ef3a24;
}
*{margin:0;padding:0;box-sizing:border-box}
html,body{width:1200px;height:2621px;overflow:hidden;background:var(--page)}
body{position:relative;font-family:"Poppins",sans-serif;color:var(--ink)}
.panel{position:absolute;background:var(--panel);overflow:hidden}
.panel > *{position:absolute}
.center{left:0;right:0;text-align:center}

/* wordmark: plain set name in the text face */
.wordmark{font-family:"Poppins",sans-serif;font-weight:500;color:var(--ink);letter-spacing:1px;text-align:center}

/* buttons */
.btn{background:var(--blue);color:var(--ink);font-weight:700;border-radius:5px;display:flex;align-items:center;justify-content:center;text-transform:uppercase}
.badge{border-radius:2px}

/* A-frame: welcome */
.aframe-welcome{left:92px;top:110px;width:474px;height:702px}
.welcome-kicker{top:187px;color:var(--blue);font-size:13px;letter-spacing:7px;font-weight:500}
.open-title{top:230px;font-family:"Roboto Slab",serif;font-weight:600;font-size:39px}
.hours{top:292px;left:64px;font-size:22px;font-weight:600;line-height:24px}
.hours .days{color:var(--blue);display:inline-block;width:133px}
.services{top:352px;font-size:21px;line-height:27px;font-weight:500;letter-spacing:.5px}
.services .bar{color:var(--blue)}
.byo{top:440px;font-size:13px;font-weight:600}
.hr-blue{height:3px;background:var(--blue);left:38px;width:398px}
.choose{top:477px;font-size:16.5px}
.prep{top:502px;font-size:14.5px;letter-spacing:.3px}
.big-phone{top:553px;font-size:50px;font-weight:700;display:flex;justify-content:center;align-items:center;gap:10px}
.web-btn{top:629px;left:68px;width:340px;height:33px;font-size:20px;text-transform:none;border-radius:8px}

/* A-frame: open */
.aframe-open{left:611px;top:110px;width:474px;height:702px}
.open-shout{top:150px;font-family:"Cinzel",serif;font-weight:600;font-size:88px;line-height:80px;letter-spacing:-1px}

/* order block */
.order-web{display:flex;gap:6px;align-items:center;justify-content:center}
.order-web .globe{width:11px;height:11px;border-radius:50%;background:var(--badge-green)}
.order-phone{font-weight:700;display:flex;align-items:center;justify-content:center;gap:5px}
.badges{display:flex}

/* takeaway cover */
.takeaway-cover{left:240px;top:849px;width:678px;height:513px}
.intro{top:166px;left:78px;width:522px;font-size:11.2px;line-height:13.2px;text-align:center;color:var(--muted)}
.notes{top:261px;font-size:10px;font-weight:600;line-height:19px;text-align:center;white-space:nowrap}
.follow{top:440px;font-size:18.5px;display:flex;gap:12px;justify-content:center;align-items:center}
.follow .ig{width:17px;height:17px;border-radius:4px;background:var(--badge-red)}

/* menu pages */
.menu-page{left:240px;width:678px;height:513px}
.menu-a{top:1398px}
.menu-b{top:1953px}
.section-title{font-family:"Roboto Slab",serif;font-weight:600;font-size:19px}
.section-title::after{content:"";display:block;width:16px;height:2px;background:var(--blue);margin-top:1px}
.list{font-size:9.4px;color:var(--muted)}
.list .row{border-bottom:1px solid var(--rule);height:16.7px;display:flex;align-items:flex-end;padding-bottom:1px}
.list .row b{color:var(--blue);font-weight:500;margin-right:3px}
.boxed{border:1px solid var(--rule);outline:1px solid var(--rule);outline-offset:-4px}
.dish{font-size:8.2px;line-height:10px;color:var(--muted);border-bottom:1px solid var(--rule);padding-bottom:8px;margin-bottom:10px}
.dish h4{color:var(--blue);font-weight:500;font-size:8.8px;margin-bottom:2px}
.lead{font-size:8.4px;color:var(--muted)}
.foot-note{font-size:8px;text-align:center;color:var(--muted)}
</style>
</head>
<body>

<!-- A-frame: welcome side -->
<section class="panel aframe-welcome">
  <div class="wordmark center" style="top:76px;font-size:32px">TIDE &amp; TATER</div>
  <p class="welcome-kicker center">WELCOME</p>
  <h1 class="open-title center">Open Every Day</h1>
  <p class="hours"><span class="days">Tues – Sun</span>Lunch 12pm – 3pm<br><span class="days">Tues – Sun</span>Dinner 5pm – 9pm</p>
  <p class="services center">DINE IN <span class="bar">|</span> TAKEAWAY<br>ONLINE ORDERING &amp; DELIVERY<br>FRESH RETAIL</p>
  <p class="byo center">BYO Welcome! Wine, Beer &amp; Spirits / Soft Drinks Available</p>
  <div class="hr-blue" style="top:468px"></div>
  <p class="choose center">Choose your preparation:</p>
  <p class="prep center">PANKO CRUMBED / TEMPURA BATTERED / GRILLED</p>
  <div class="hr-blue" style="top:525px"></div>
  <p class="big-phone center">
    <svg width="46" height="38" viewBox="0 0 46 38" aria-hidden="true"><path d="M4 12 Q23 -2 42 12 L38 18 L31 14 L31 9 Q23 6 15 9 L15 14 L8 18 Z" fill="#fff"/><path d="M12 17 H34 L40 36 H6 Z" fill="#fff"/><g fill="#231f20"><rect x="16" y="22" width="3" height="3"/><rect x="22" y="22" width="3" height="3"/><rect x="28" y="22" width="3" height="3"/><rect x="16" y="28" width="3" height="3"/><rect x="22" y="28" width="3" height="3"/><rect x="28" y="28" width="3" height="3"/></g></svg>
    3490 2218</p>
  <div class="btn web-btn">www.tideandtater.com.au</div>
</section>

<!-- A-frame: we're open side -->
<section class="panel aframe-open">
  <div class="wordmark center" style="top:54px;font-size:32px">TIDE &amp; TATER</div>
  <h2 class="open-shout center">WE’RE<br>OPEN!</h2>
  <div class="btn" style="top:386px;left:134px;width:209px;height:34px;font-size:17px">Order for pickup</div>
  <p class="order-web center" style="top:434px;font-size:15px"><span class="globe"></span>www.tideandtater.com.au</p>
  <p class="order-phone center" style="top:454px;font-size:29px">☎ 3490 2218</p>
  <div class="btn" style="top:522px;left:134px;width:209px;height:34px;font-size:17px">Order for delivery</div>
  <div class="badges" style="top:576px;left:135px;gap:4px">
    <span class="badge" style="width:35px;height:34px;background:var(--badge-green)"></span>
    <span class="badge" style="width:79px;height:34px;background:var(--badge-yellow)"></span>
    <span class="badge" style="width:87px;height:34px;background:var(--badge-teal)"></span>
  </div>
  <div class="badges" style="top:621px;left:135px;gap:14px">
    <span class="badge" style="width:90px;height:20px;background:var(--badge-orange)"></span>
    <span class="badge" style="width:108px;height:20px;background:var(--badge-red)"></span>
  </div>
</section>

<!-- Takeaway menu: cover -->
<section class="panel takeaway-cover">
  <div class="wordmark center" style="top:60px;font-size:44px">TIDE &amp; TATER</div>
  <p class="intro">Our premium quality fish is wild caught and sustainably farmed from pristine Australian &amp; New Zealand waters, delivered in-store every day for you to enjoy! Our seafood is deep-fried to golden goodness with premium 100% Australian grown and pressed sunflower oil.<br><span style="line-height:24px">(All seafood is subject to daily fresh market availability).</span></p>
  <p class="notes" style="left:100px;width:244px">Gluten friendly options are available.<br>Our takeaway packaging is eco friendly.</p>
  <p class="notes" style="left:342px;width:244px">Menu substitutions are not available.<br>Public Holiday surcharge 15%.</p>
  <div class="btn" style="top:340px;left:161px;width:148px;height:23px;font-size:11.5px">Order for pickup</div>
  <div class="btn" style="top:340px;left:349px;width:148px;height:23px;font-size:11.5px">Order for delivery</div>
  <p class="order-web" style="top:378px;left:150px;width:170px;font-size:10.5px"><span class="globe" style="width:8px;height:8px"></span>www.tideandtater.com.au</p>
  <p class="order-phone" style="top:394px;left:150px;width:170px;font-size:14px">☎ 3490 2218</p>
  <div class="badges" style="top:375px;left:349px;gap:3px">
    <span class="badge" style="width:24px;height:24px;background:var(--badge-green)"></span>
    <span class="badge" style="width:55px;height:24px;background:var(--badge-yellow)"></span>
    <span class="badge" style="width:62px;height:24px;background:var(--badge-teal)"></span>
  </div>
  <div class="badges" style="top:406px;left:349px;gap:10px">
    <span class="badge" style="width:62px;height:13px;background:var(--badge-orange)"></span>
    <span class="badge" style="width:76px;height:13px;background:var(--badge-red)"></span>
  </div>
  <p class="follow center" style="top:440px">Follow us <span class="ig"></span> tideandtater_riverside</p>
</section>

<!-- Takeaway menu: chips, starters, burgers -->
<section class="panel menu-page menu-a">
  <h3 class="section-title" style="top:35px;left:45px">Chips</h3>
  <div class="list" style="top:68px;left:45px;width:272px">
    <div class="row">Chips GF</div><div class="row">Beer Battered Chips</div><div class="row">Sweet Potato Chips</div>
  </div>
  <h3 class="section-title" style="top:172px;left:45px">Starters &amp; Sides</h3>
  <div class="list" style="top:204px;left:45px;width:272px">
    <div class="row">Crumbed Calamari (8)</div><div class="row">Salt &amp; Pepper Calamari (8)</div><div class="row">Crumbed Sea Scallop</div><div class="row">Crumbed Prawn</div><div class="row">BBQ Prawn Skewer</div><div class="row">Onion Rings (8)</div><div class="row">Popcorn Chicken</div><div class="row">Potato Scallop</div><div class="row">Grilled Halloumi (3 slices)</div><div class="row">Fried Halloumi (3 slices, crumbed)</div>
  </div>
  <div class="boxed" style="top:24px;left:351px;width:282px;height:250px"></div>
  <h3 class="section-title" style="top:35px;left:361px">Burgers &amp; Tacos</h3>
  <div style="top:73px;left:361px;width:262px">
    <div class="dish"><h4>Fish Burger &amp; Chips</h4>Crumbed cod fillet, shredded lettuce, tomato &amp; tartare sauce in a toasted bun.</div>
    <div class="dish"><h4>Fish Tacos (3) &amp; Chips</h4>Beer battered cod, shredded red &amp; green cabbage, carrot, chipotle mayonnaise in soft flour tortillas.</div>
    <div class="dish"><h4>Chicken Burger &amp; Chips</h4>Grilled free range chicken tenders, shredded lettuce, tomato, cheese, avocado, aioli in a toasted bun.</div>
    <div class="dish" style="border:0"><h4>Steak Burger &amp; Chips</h4>Grilled grass fed rib fillet, shredded lettuce, tomato, cheese, caramelised onion, BBQ sauce in a toasted bun</div>
  </div>
  <h3 class="section-title" style="top:318px;left:351px">Children’s Fish &amp; Chips</h3>
  <div class="list" style="top:348px;left:351px;width:277px">
    <div class="row"><b>Fish Finger</b>(4) &amp; chips</div><div class="row"><b>Crumbled Calamari</b>(4) &amp; chips</div><div class="row"><b>Popcorn Chicken</b>&amp; chips</div>
  </div>
  <h3 class="section-title" style="top:414px;left:351px">Sauces</h3>
  <div class="list" style="top:440px;left:351px;width:277px;font-weight:600;color:var(--ink)">
    <div class="row" style="height:18px">Tartare, Aioli, Tomato &amp; Chipotle Mayonaise</div>
  </div>
</section>

<!-- Takeaway menu: fish & chips, salads, platters -->
<section class="panel menu-page menu-b">
  <div class="boxed" style="top:23px;left:45px;width:282px;height:246px"></div>
  <h3 class="section-title" style="top:34px;left:55px">Fish &amp; Chips</h3>
  <p class="lead" style="top:60px;left:55px">Served with your choice of chips, tartare sauce &amp; lemon.</p>
  <div class="list" style="top:72px;left:55px;width:261px;font-size:8.6px">
    <div class="row"><b>Cod &amp; chips</b>(NZ, wild caught)</div><div class="row"><b>Whiting &amp; chips</b>(QLD, wild caught, crumbed only)</div><div class="row"><b>Flathead &amp; chips</b>(SA, wild caught, beer battered only)</div><div class="row"><b>Snapper &amp; chips</b>(NT, wild caught)</div><div class="row"><b>Barramundi &amp; chips</b>(NT, ocean farmed)</div><div class="row"><b>Salmon &amp; chips</b>(TAS, ocean farmed)</div><div class="row"><b>Crumbed Calamari</b>(8) &amp; chips</div><div class="row"><b>Salt &amp; Pepper Calamari</b>(8) &amp; chips</div><div class="row"><b>Crumbed Prawns</b>(5) &amp; chips</div><div class="row" style="border:0"><b>BBQ Prawn Skewers</b>(2) &amp; chips</div>
  </div>
  <p class="foot-note" style="top:242px;left:55px;width:261px">Made fresh to order | Choose your preparation:<br><b style="color:var(--ink)">GRILLED / CRUMBED / BEER BATTERED</b></p>
  <h3 class="section-title" style="top:33px;left:351px">Salads</h3>
  <p class="lead" style="top:65px;left:351px;color:var(--ink);font-weight:500">Freshly prepared to order using the freshest local produce.</p>
  <div style="top:99px;left:351px;width:282px">
    <div class="dish" style="font-size:7.4px;line-height:9px;padding-bottom:9px;margin-bottom:12px"><h4>Greek</h4>Lettuce, cucumber, tomato, red onion, Kalamata olives, feta, Greek peppers, wild oregano, dressed in Greek extra virgin olive oil vinaigrette.</div>
    <div class="dish" style="font-size:7.4px;line-height:9px;padding-bottom:9px;margin-bottom:12px"><h4>Roast Pumpkin</h4>Roast pumpkin, wild rocket, Parmigiano Reggiano, toasted pine nuts, dressed in Greek extra virgin olive oil &amp; vintage balsamic vinegar.</div>
    <div class="dish" style="font-size:7.4px;line-height:9px;padding-bottom:9px;margin-bottom:12px"><h4>Slaw</h4>Shredded red &amp; green cabbage, carrot, tossed in a light mayonnaise dressing.</div>
    <div class="dish" style="font-size:7.4px;line-height:9px;border:0"><h4>Asian Slaw</h4>Shredded red &amp; green cabbage, carrot, spring onion, crispy noodles, sesame seeds, tossed in a sweet soy dressing.</div>
  </div>
  <h3 class="section-title" style="top:350px;left:45px">Cooked Seafood Platters</h3>
  <p class="lead" style="top:380px;left:45px;width:590px;line-height:10px">Cooked Seafood Platters include: whiting, calamari, salt &amp; pepper calamari, prawns, sea scallops, chips, one of our freshly made salads, sauce &amp; lemon.</p>
  <div class="list" style="top:410px;left:45px;width:588px;font-size:8.4px;font-weight:600;color:var(--ink)">
    <div class="row" style="height:17.5px">Cooked Platter for One</div><div class="row" style="height:17.5px">Cooked Platter for Two</div><div class="row" style="height:17.5px">Cooked Platter for Three</div>
  </div>
  <p class="foot-note center" style="top:469px">Our seafood platters are available crumbed only.</p>
</section>

</body>
</html>
```